ReelBloom business card

We are a performing arts company providing training (to both kids and adults) as well as performers for events. We hope to bring joy and confidence on stage to the people we train, as well as joy to the audience when our artistes perform. Designs should convey the joy, confidence and vibrancy on stage. Design business card using the attached logo. Card to include name, mobile tel, email address, company address, and website. Double sided. To also include the following list of what the company does:
• Training & Enrichment
• Private & Corporate Entertainment
- Music composition & production

Industry/Entity Type

Training

Contact Information for Business Card

Card to include name, mobile tel, email address, company address, and website. Double sided. To also include the following list of what the company does:
• Training & Enrichment

Requirements
Nice to have
• Card need not be the traditional rectangular in shape but not too outrageous.

```html
<!DOCTYPE html>
<html lang="en">
<head>
<meta charset="utf-8">
<title>ReelBloom business card</title>
<link rel="stylesheet" href="https://fonts.googleapis.com/css2?family=Arimo:wght@400;700&family=PT+Serif:wght@700&display=swap">
<style>
  :root {
    --stage-bg: #ecebe8;
    --card-white: #ffffff;
    --bloom-pink: #f2256f;
    --ink-navy: #24306b;
    --note-grey: #d9d9d9;
    --note-grey-soft: #f1f1f1;
    --edge-shadow: rgba(0,0,0,0.18);
  }
  * { box-sizing: border-box; margin: 0; padding: 0; }
  html, body { width: 1200px; height: 886px; overflow: hidden; }
  body {
    background: var(--stage-bg);
    font-family: "Arimo", Arial, sans-serif;
    position: relative;
  }
  .card {
    position: absolute;
    top: 288px;
    width: 540px;
    height: 310px;
    background: var(--card-white);
    border-radius: 16px;
    overflow: hidden;
    box-shadow: 0 6px 18px var(--edge-shadow);
  }
  .card--front { left: 30px; }
  .card--back { left: 630px; }

  .music-decor {
    position: absolute;
    background: linear-gradient(160deg, var(--note-grey-soft) 0%, var(--note-grey) 45%, var(--note-grey-soft) 100%);
    opacity: 0.8;
  }
  .card--front .music-decor { left: 0; top: 0; width: 290px; height: 310px;
    background: radial-gradient(ellipse at 60% 50%, var(--card-white) 38%, var(--note-grey) 75%, var(--note-grey-soft) 100%); }
  .card--back .music-decor { right: 0; top: 30px; width: 300px; height: 220px; opacity: 0.5;
    border-radius: 50% 0 0 50%; }

  .brand {
    position: absolute;
    display: flex;
    align-items: center;
    gap: 10px;
  }
  .brand__dot {
    width: 22px; height: 22px; border-radius: 50%;
    background: var(--ink-navy);
  }
  .brand__name {
    font-family: "Arimo", Arial, sans-serif;
    font-weight: 700;
    font-size: 38px;
    color: var(--ink-navy);
    letter-spacing: -0.5px;
    white-space: nowrap;
  }
  .card--front .brand { left: 42px; top: 130px; }
  .card--back .brand { left: 250px; top: 70px; }

  .contact-band {
    position: absolute;
    left: 290px; top: 0;
    width: 250px; height: 310px;
    background: var(--bloom-pink);
  }
  .contact-band::before {
    content: "";
    position: absolute;
    left: 8px; top: 0; bottom: 0;
    width: 2px;
    background: var(--card-white);
  }
  .holder {
    position: absolute;
    right: 22px; top: 34px;
    text-align: right;
    color: var(--card-white);
  }
  .holder__name {
    font-family: "PT Serif", Georgia, serif;
    font-size: 25px;
    white-space: nowrap;
  }
  .holder__role { font-size: 12px; margin-top: 2px; }

  .contact-list {
    position: absolute;
    left: 30px; bottom: 34px;
    list-style: none;
    color: var(--card-white);
    font-size: 13px;
    line-height: 1.25;
  }
  .contact-list li {
    display: flex;
    align-items: flex-start;
    gap: 10px;
    margin-top: 6px;
    white-space: nowrap;
  }
  .contact-list svg { width: 13px; height: 13px; flex: none; margin-top: 1px; }

  .services {
    position: absolute;
    left: 54px; top: 150px;
    color: var(--bloom-pink);
  }
  .services__title {
    font-family: "PT Serif", Georgia, serif;
    font-size: 24px;
    margin-bottom: 10px;
  }
  .services__list { list-style: none; font-size: 15px; line-height: 1.45; white-space: nowrap; }
</style>
</head>
<body>
  <section class="card card--front" aria-label="Card front">
    <div class="music-decor" role="img" aria-label="Flowing music staff with notes and clefs, grey on white"></div>
    <div class="brand">
      <span class="brand__dot"></span>
      <span class="brand__name">ReelBloom</span>
    </div>
    <div class="contact-band">
      <div class="holder">
        <p class="holder__name">Employee name</p>
        <p class="holder__role">Managing Director</p>
      </div>
      <ul class="contact-list">
        <li>
          <svg viewBox="0 0 16 16" fill="currentColor"><path d="M4 1l3 3-2 2c1 2 3 4 5 5l2-2 3 3-2 3C7 15 1 9 1 3z"/></svg>
          <span>555-0142 7788</span>
        </li>
        <li>
          <svg viewBox="0 0 16 16" fill="none" stroke="currentColor" stroke-width="1.6"><rect x="4" y="1" width="8" height="14" rx="1.5"/></svg>
          <span>555-0199 3064</span>
        </li>
        <li>
          <svg viewBox="0 0 16 16" fill="none" stroke="currentColor" stroke-width="1.6"><rect x="1" y="3" width="14" height="10"/><path d="M1 3l7 6 7-6"/></svg>
          <span>hello@reelbloom.art</span>
        </li>
        <li>
          <svg viewBox="0 0 16 16" fill="none" stroke="currentColor" stroke-width="1.4"><circle cx="8" cy="8" r="6.5"/><path d="M1.5 8h13M8 1.5c-3 3.5-3 9.5 0 13M8 1.5c3 3.5 3 9.5 0 13"/></svg>
          <span>www.reelbloom.art</span>
        </li>
        <li>
          <svg viewBox="0 0 16 16" fill="currentColor"><path d="M8 1a5 5 0 0 0-5 5c0 4 5 9 5 9s5-5 5-9a5 5 0 0 0-5-5zm0 7a2 2 0 1 1 0-4 2 2 0 0 1 0 4z"/></svg>
          <span>18 Maple Row, Linden Park,<br>NJ 07999</span>
        </li>
      </ul>
    </div>
  </section>

  <section class="card card--back" aria-label="Card back">
    <div class="music-decor" role="img" aria-label="Faint flowing music staff with notes"></div>
    <div class="brand">
      <span class="brand__dot"></span>
      <span class="brand__name">ReelBloom</span>
    </div>
    <div class="services">
      <h2 class="services__title">Service</h2>
      <ul class="services__list">
        <li>Training &amp; Enrichment</li>
        <li>Private &amp; Corporate Entertainment</li>
        <li>Music composition &amp; production</li>
      </ul>
    </div>
  </section>
</body>
</html>
```